VelkaVision.com

Complete Website Design (Godaddy) and company Branding / Logo Design. The products will sell are only done in-person and are installed. So this site does not need to be an e-commerce site. We will only be giving out information and collecting customer inquires. Website will only need to be about 3 to 5 pages.

```html
<!DOCTYPE html>
<html lang="en">
<head>
<meta charset="utf-8">
<title>VelkaVision</title>
<link rel="stylesheet" href="https://fonts.googleapis.com/css2?family=Montserrat:wght@500;600;700;800&family=Libre+Franklin:wght@400;500&display=swap">
<style>
:root{
  --red:#ee1d36;
  --ink:#111111;
  --text:#222222;
  --muted:#8a8a8a;
  --soft:#f7f7f7;
  --white:#ffffff;
  --black:#000000;
}
*{margin:0;padding:0;box-sizing:border-box}
html,body{width:1200px;height:2644px;overflow:hidden;background:var(--white)}
body{position:relative;font-family:"Libre Franklin",Arial,sans-serif;color:var(--text)}
.abs{position:absolute}
.head{font-family:"Montserrat",Arial,sans-serif;font-weight:700}

/* header */
.brand{left:110px;top:34px;font-family:"Montserrat",sans-serif;font-weight:800;font-size:38px;color:var(--ink);letter-spacing:.5px}
.btn-outline,.btn-solid{font-family:"Montserrat",sans-serif;font-weight:700;font-size:13px;display:flex;align-items:center;justify-content:center}
.btn-outline{left:840px;top:13px;width:111px;height:41px;border:2px solid var(--red);color:var(--red)}
.btn-solid{left:970px;top:13px;width:118px;height:41px;background:var(--red);color:var(--white)}
.nav{top:79px;font-size:16px;color:var(--ink)}

/* hero */
.hero{left:3px;top:120px;width:1192px;height:551px;border-radius:42px;overflow:hidden;
  background:linear-gradient(90deg,#8f8c88 0%,#b5b1ab 40%,#6a6460 60%,#9f8f82 85%,#c9bdb1 100%)}
.hero-shade{left:0;top:0;width:100%;height:100%;background:linear-gradient(90deg,rgba(0,0,0,.35),rgba(0,0,0,0) 55%)}
.hero-kicker{left:112px;top:293px;font-size:37px;color:var(--red);font-weight:800}
.hero-title{left:108px;top:330px;font-size:72px;color:var(--white);font-weight:800;letter-spacing:1px}
.hero-cta{left:113px;top:429px;width:163px;height:49px;border:2px solid var(--red);color:var(--white);font-family:"Montserrat",sans-serif;font-weight:700;font-size:15px;display:flex;align-items:center;justify-content:center}
.dots{left:578px;top:603px;display:flex;gap:3px}
.dots span{width:8px;height:8px;border-radius:50%;background:var(--white)}
.dots span.on{background:var(--red)}

/* about */
.label{font-family:"Montserrat",sans-serif;font-weight:700;color:var(--red)}
.about-label{left:112px;top:784px;font-size:20px}
.about-title{left:111px;top:812px;font-size:36px;color:var(--ink);font-weight:800}
.about-lead{left:113px;top:874px;width:470px;font-family:"Montserrat",sans-serif;font-weight:500;font-size:26px;line-height:44.5px;color:var(--ink)}
.about-copy{left:691px;top:770px;width:380px;font-size:15px;line-height:25.7px;color:var(--ink)}
.frame{left:555px;top:1045px;width:396px;height:380px;border:4px solid var(--red)}
.photo-right{left:609px;top:994px;width:479px;height:326px;background:linear-gradient(120deg,#3f5a73 0%,#cfd3d6 45%,#eef0f1 70%,#4d7a68 100%)}
.photo-left{left:112px;top:1117px;width:604px;height:338px;background:linear-gradient(90deg,#d8d8d6 0%,#2a2d33 20%,#cfcfcd 45%,#2e57c8 70%,#d6d6d4 100%)}

/* contact */
.contact-band{left:0;top:1576px;width:1200px;height:609px;background:var(--soft)}
.contact-card{left:463px;top:1650px;width:737px;height:468px;background:var(--white)}
.contact-bar{left:455px;top:1660px;width:7px;height:420px;background:var(--red)}
.person{left:0;top:1576px;width:430px;height:609px;background:linear-gradient(180deg,#e9ecef 0%,#a9bccb 30%,#5b7e99 65%,#6b6d70 100%)}
.quote-label{left:581px;top:1700px;font-size:20px}
.quote-title{left:578px;top:1722px;font-size:36px;color:var(--ink);font-weight:800}
.field{left:574px;width:250px;height:52px;background:var(--white);box-shadow:0 4px 18px rgba(0,0,0,.06);font-size:16px;color:var(--muted);padding:17px 19px}
.message{left:840px;top:1790px;width:237px;height:253px;background:var(--white);box-shadow:0 4px 22px rgba(0,0,0,.07);font-size:16px;color:var(--muted);padding:17px 23px}
.submit{left:574px;top:1995px;width:250px;height:52px;background:var(--red);color:var(--white);font-family:"Montserrat",sans-serif;font-weight:700;font-size:16px;display:flex;align-items:center;justify-content:center}

/* footer */
.footer{left:0;top:2185px;width:1200px;height:459px;background:var(--black)}
.f-head{top:2283px;font-size:20px;color:var(--white);font-weight:700}
.f-rule{width:30px;height:2px;background:var(--red)}
.f-item{font-size:16px;color:var(--white);display:flex;align-items:center;gap:9px}
.f-item svg{flex:none}
.f-input{left:846px;width:243px;height:1px;background:#666}
.f-ph{font-size:15px;color:#cfcfcf}
.f-btn{left:846px;top:2452px;width:145px;height:40px;background:var(--red);color:var(--white);font-family:"Montserrat",sans-serif;font-weight:700;font-size:13px;display:flex;align-items:center;justify-content:center;box-shadow:0 6px 16px rgba(238,29,54,.35)}
.f-divider{left:113px;top:2537px;width:975px;height:1px;background:#333}
.copyright{left:0;top:2575px;width:1200px;text-align:center;font-size:16px;color:var(--white)}
</style>
</head>
<body>

<header>
  <div class="abs brand">VELKAVISION</div>
  <div class="abs btn-outline">SIGN UP</div>
  <div class="abs btn-solid">LOG IN</div>
  <nav>
    <span class="abs nav" style="left:618px">Home</span>
    <span class="abs nav" style="left:707px">About</span>
    <span class="abs nav" style="left:796px">Services</span>
    <span class="abs nav" style="left:898px">News</span>
    <span class="abs nav" style="left:987px">Contact</span>
  </nav>
</header>

<section class="abs hero" role="img" aria-label="Two installers mounting a large flat-screen TV on a living room wall">
  <div class="abs hero-shade"></div>
</section>
<div class="abs head hero-kicker">WELCOME TO</div>
<div class="abs head hero-title">VELKAVISION</div>
<div class="abs hero-cta">GET STARTED</div>
<div class="abs dots"><span></span><span class="on"></span><span></span><span></span></div>

<section>
  <div class="abs label about-label">ABOUT</div>
  <h2 class="abs head about-title">ABOUT VELKAVISION</h2>
  <p class="abs about-lead">Lorem ipsum dolor sit amet, consectetur adipiscing elit, sed do eiusmod tempor incididunt ut labore et dolore magna aliqua.</p>
  <p class="abs about-copy">Lorem ipsum dolor sit amet, consectetur adipiscing elit, sed do eiusmod tempor incididunt ut labore et dolore magna aliqua. Quis ipsum suspendisse ultrices gravida. Risus commodo viverra maecenas accumsan lacus vel facilisis. Lorem ipsum dolor sit amet, consectetur adipiscing elit, sed do eiusmod tempor incididunt ut labore et dolore magna aliqua.</p>
  <div class="abs frame"></div>
  <div class="abs photo-right" role="img" aria-label="Technician connecting cables to a ceiling-mounted projector"></div>
  <div class="abs photo-left" role="img" aria-label="Technician in blue overalls connecting a cable behind a TV on a stand"></div>
</section>

<section>
  <div class="abs contact-band"></div>
  <div class="abs contact-card"></div>
  <div class="abs contact-bar"></div>
  <div class="abs person" role="img" aria-label="Installer in a cap and work shirt holding a toolbox"></div>
  <div class="abs label quote-label">REQUEST A QUOTE</div>
  <h2 class="abs head quote-title">CONTACT US</h2>
  <div class="abs field" style="top:1790px">Name</div>
  <div class="abs field" style="top:1858px">Phone</div>
  <div class="abs field" style="top:1926px">Email</div>
  <div class="abs message">Type your message</div>
  <div class="abs submit">SUBMIT</div>
</section>

<footer>
  <div class="abs footer"></div>

  <div class="abs head f-head" style="left:113px">CONTACT</div>
  <div class="abs f-rule" style="left:113px;top:2314px"></div>
  <div class="abs f-item" style="left:115px;top:2338px;align-items:flex-start;line-height:26px">
    <svg width="12" height="16" viewBox="0 0 12 16" style="margin-top:4px"><path d="M6 0a6 6 0 0 0-6 6c0 4.5 6 10 6 10s6-5.5 6-10a6 6 0 0 0-6-6zm0 8.5A2.5 2.5 0 1 1 6 3.5a2.5 2.5 0 0 1 0 5z" fill="#ee1d36"/></svg>
    <span>Lorem ipsum dolor<br>sit amet</span>
  </div>
  <div class="abs f-item" style="left:115px;top:2402px">
    <svg width="13" height="13" viewBox="0 0 24 24"><path d="M6.6 10.8a15.2 15.2 0 0 0 6.6 6.6l2.2-2.2a1 1 0 0 1 1-.25 11.4 11.4 0 0 0 3.6.57 1 1 0 0 1 1 1V20a1 1 0 0 1-1 1A17 17 0 0 1 3 4a1 1 0 0 1 1-1h3.5a1 1 0 0 1 1 1c0 1.25.2 2.45.57 3.57a1 1 0 0 1-.25 1z" fill="#ee1d36"/></svg>
    <span>+1 555 014 2290</span>
  </div>
  <div class="abs f-item" style="left:115px;top:2440px">
    <svg width="16" height="12" viewBox="0 0 16 12"><rect width="16" height="12" rx="1.5" fill="#ee1d36"/><path d="M1 1.5l7 5 7-5" stroke="#000" stroke-width="1.4" fill="none"/></svg>
    <span>hello@velkavision.com</span>
  </div>

  <div class="abs head f-head" style="left:402px">HELP LINK</div>
  <div class="abs f-rule" style="left:402px;top:2314px"></div>
  <div class="abs f-item" style="left:406px;top:2338px"><svg width="7" height="10" viewBox="0 0 7 10"><path d="M1 1l4 4-4 4" stroke="#fff" stroke-width="1.4" fill="none"/></svg><span>Terms &amp; Condtions</span></div>
  <div class="abs f-item" style="left:406px;top:2368px"><svg width="7" height="10" viewBox="0 0 7 10"><path d="M1 1l4 4-4 4" stroke="#fff" stroke-width="1.4" fill="none"/></svg><span>Privacy Policy</span></div>
  <div class="abs f-item" style="left:406px;top:2398px"><svg width="7" height="10" viewBox="0 0 7 10"><path d="M1 1l4 4-4 4" stroke="#fff" stroke-width="1.4" fill="none"/></svg><span>About Us</span></div>
  <div class="abs f-item" style="left:406px;top:2428px"><svg width="7" height="10" viewBox="0 0 7 10"><path d="M1 1l4 4-4 4" stroke="#fff" stroke-width="1.4" fill="none"/></svg><span>Support</span></div>

  <div class="abs head f-head" style="left:629px;top:2287px">FOLLOW US</div>
  <div class="abs f-rule" style="left:629px;top:2318px"></div>
  <div class="abs f-item" style="left:632px;top:2336px"><svg width="12" height="12"><circle cx="6" cy="6" r="5" fill="#fff"/></svg><span>Friendhub</span></div>
  <div class="abs f-item" style="left:632px;top:2366px"><svg width="12" height="12"><circle cx="6" cy="6" r="5" fill="#fff"/></svg><span>Snapgram</span></div>
  <div class="abs f-item" style="left:632px;top:2396px"><svg width="12" height="12"><circle cx="6" cy="6" r="5" fill="#fff"/></svg><span>Chirper</span></div>
  <div class="abs f-item" style="left:632px;top:2426px"><svg width="12" height="12"><circle cx="6" cy="6" r="5" fill="#fff"/></svg><span>Vidstream</span></div>

  <div class="abs head f-head" style="left:843px">NEWSLETTER UPDATES</div>
  <div class="abs f-rule" style="left:845px;top:2314px"></div>
  <div class="abs f-ph" style="left:847px;top:2337px">Name*</div>
  <div class="abs f-input" style="top:2366px"></div>
  <div class="abs f-ph" style="left:847px;top:2388px">Email*</div>
  <div class="abs f-input" style="top:2418px"></div>
  <div class="abs f-btn">SUBMIT NOW</div>

  <div class="abs f-divider"></div>
  <div class="abs copyright">©Copyrights 2024&nbsp; VelkaVision.&nbsp; |&nbsp;&nbsp;&nbsp; All Rights Reserved</div>
</footer>

</body>
</html>
```